Business Card Design - ChoiceCraft

Looking for creative, modern design, two sided for ChoiceCraft that is consistent with color and feel of website www.choicecraftpro.net.
Updates

Back of card will be used to promote products or have a quote revolving around decisions, change, leadership, innovation, creativity. Back should also have space to promote website, but optional to use the icon. Front of the card will need to use the icon and have standard place for name, job title, phone and email. We are not looking to put a mailing address or fax. Also want space to place a few words/phrase explaining what we do...such as individual growth and organizational development or tools, training, information...in addition, want the facebook icon small on the front somewhere as we are also on facebook.

Vector file uploaded of icon.

Target Market(s)

Professional coaching for individual growth and organizational development

Industry/Entity Type

Business

Requirements
Must have
• Icon...see attached.

```html
<!DOCTYPE html>
<html lang="en">
<head>
<meta charset="utf-8">
<title>ChoiceCraft Business Card</title>
<link href="https://fonts.googleapis.com/css2?family=Open+Sans:wght@400;600;700&family=Arimo:wght@400;700&display=swap" rel="stylesheet">
<style>
  :root {
    --backdrop: #e4e6e8;
    --card-white: #ffffff;
    --sky-light: #8fd0f0;
    --sky: #35b1e6;
    --sky-deep: #1fa6e2;
    --navy-swoosh: #1d6fc0;
    --ink: #1a1a1a;
    --ink-soft: #555555;
    --on-blue: #ffffff;
    --mark-light: #d7e3f1;
    --mark-dark: #3f86cf;
  }
  * { margin: 0; padding: 0; box-sizing: border-box; }
  html, body {
    width: 1200px;
    height: 1069px;
    overflow: hidden;
    background: var(--backdrop);
  }
  .card {
    position: absolute;
    border-radius: 22px;
    overflow: hidden;
    box-shadow: 0 4px 14px rgba(0,0,0,0.18);
  }
  .card-front {
    left: 77px; top: 77px;
    width: 765px; height: 436px;
    background: var(--card-white);
  }
  .card-back {
    left: 361px; top: 581px;
    width: 761px; height: 437px;
    background: linear-gradient(90deg, var(--sky-light) 0%, var(--sky) 75%, var(--sky-deep) 100%);
  }
  .front-waves { position: absolute; inset: 0; }
  .brand-mark {
    position: absolute;
    left: 88px; top: 18px;
    width: 160px; height: 160px;
  }
  .brand-name {
    position: absolute;
    left: 50px; top: 232px;
    font-family: "Open Sans", sans-serif;
    font-weight: 700;
    font-size: 31px;
    color: var(--ink);
    letter-spacing: 0.2px;
  }
  .holder {
    position: absolute;
    left: 64px; top: 298px;
    font-family: "Open Sans", sans-serif;
    font-size: 22px;
    color: var(--ink-soft);
  }
  .holder strong { font-weight: 700; font-size: 25px; }
  .contact-list {
    position: absolute;
    right: 17px; top: 226px;
    list-style: none;
    text-align: right;
    font-family: "Open Sans", sans-serif;
    font-size: 18.5px;
    line-height: 26.5px;
    color: var(--on-blue);
  }
  .contact-list li { display: flex; justify-content: flex-end; align-items: center; gap: 7px; }
  .contact-list svg { width: 14px; height: 14px; flex: none; }
  .social-dot { width: 12px; height: 12px; background: var(--on-blue); border-radius: 2px; opacity: 0.85; }
  .tagline {
    position: absolute;
    right: 17px; top: 350px;
    text-align: right;
    font-family: "Open Sans", sans-serif;
    font-size: 23px;
    line-height: 31px;
    color: var(--on-blue);
  }
  .quote-list {
    position: absolute;
    left: 52px; top: 36px;
    list-style: none;
    font-family: "Arimo", sans-serif;
    color: var(--on-blue);
  }
  .quote { margin-bottom: 21px; }
  .quote:nth-child(3) { margin-bottom: 24px; }
  .quote-text { font-size: 19px; line-height: 27px; }
  .quote-text .mark-open { font-weight: 700; font-size: 22px; vertical-align: 6px; margin-right: 3px; }
  .quote-text .mark-close { font-weight: 700; font-size: 30px; vertical-align: -10px; margin-left: 3px; line-height: 0; }
  .quote-author { font-size: 19px; font-weight: 700; padding-left: 4px; line-height: 24px; }
  .back-mark {
    position: absolute;
    left: 540px; top: 278px;
    width: 150px; height: 150px;
  }
</style>
</head>
<body>

<section class="card card-front" aria-label="Card front">
  <svg class="front-waves" viewBox="0 0 765 436" preserveAspectRatio="none" aria-hidden="true">
    <defs>
      <linearGradient id="frontBlue" x1="0" y1="0" x2="1" y2="0">
        <stop offset="0" stop-color="#8fd0f0"/>
        <stop offset="0.6" stop-color="#35b1e6"/>
        <stop offset="1" stop-color="#1fa6e2"/>
      </linearGradient>
    </defs>
    <path d="M765,12 C650,150 470,300 0,350 L0,436 L765,436 Z" fill="url(#frontBlue)"/>
    <path d="M0,328 C170,390 400,340 555,262 C400,360 170,410 0,372 Z" fill="#1d6fc0"/>
    <path d="M0,372 C170,410 400,360 555,262 C410,372 180,420 0,384 Z" fill="#ffffff"/>
  </svg>

  <svg class="brand-mark" viewBox="0 0 160 160" role="img" aria-label="ChoiceCraft icon">
    <circle cx="80" cy="80" r="78" fill="var(--mark-dark)"/>
  </svg>

  <div class="brand-name">ChoiceCraft</div>
  <div class="holder"><strong>Your Name,</strong> Title</div>

  <ul class="contact-list">
    <li>
      <svg viewBox="0 0 14 14" aria-hidden="true"><circle cx="7" cy="7" r="6" fill="none" stroke="#fff" stroke-width="1.4"/><path d="M4.5 4 L6 4 L6.5 6 L5.6 6.6 Q6.5 8.4 8 8.9 L8.6 8 L10 8.6 L10 10 Q6 10.5 4.5 4 Z" fill="#fff"/></svg>
      123-456-789
    </li>
    <li>
      <svg viewBox="0 0 14 14" aria-hidden="true"><rect x="1" y="3" width="12" height="8" rx="1" fill="#fff"/><path d="M1.5 3.5 L7 8 L12.5 3.5" fill="none" stroke="#35b1e6" stroke-width="1.2"/></svg>
      info@choicemail.net
    </li>
    <li><span class="social-dot" aria-hidden="true"></span>/choicecraftpro</li>
    <li>
      <svg viewBox="0 0 14 14" aria-hidden="true"><circle cx="7" cy="7" r="6" fill="none" stroke="#fff" stroke-width="1.3"/><ellipse cx="7" cy="7" rx="2.6" ry="6" fill="none" stroke="#fff" stroke-width="1"/><line x1="1" y1="7" x2="13" y2="7" stroke="#fff" stroke-width="1"/></svg>
      www.choicecraftpro.net
    </li>
  </ul>

  <p class="tagline">Supporting individual growth<br>and organizational development.</p>
</section>

<section class="card card-back" aria-label="Card back">
  <ul class="quote-list">
    <li class="quote">
      <div class="quote-text"><span class="mark-open">&ldquo;</span>Try not to become a man of success, but rather a man of value.<span class="mark-close">&rdquo;</span></div>
      <div class="quote-author">- Alden Ellery</div>
    </li>
    <li class="quote">
      <div class="quote-text"><span class="mark-open">&ldquo;</span>The only constant is change.<span class="mark-close">&rdquo;</span></div>
      <div class="quote-author">- Theron Kallis</div>
    </li>
    <li class="quote">
      <div class="quote-text"><span class="mark-open">&ldquo;</span>We are what we repeatedly do. Excellence is not an act, it is a habit.<span class="mark-close">&rdquo;</span></div>
      <div class="quote-author">- Aristo Venn</div>
    </li>
    <li class="quote">
      <div class="quote-text"><span class="mark-open">&ldquo;</span>Simplicity is the ultimate sophistication.<span class="mark-close">&rdquo;</span></div>
      <div class="quote-author">- Lorenzo DaVelli</div>
    </li>
    <li class="quote">
      <div class="quote-text"><span class="mark-open">&ldquo;</span>Life is not fair - get used to it.<span class="mark-close">&rdquo;</span></div>
      <div class="quote-author">- Will Garner</div>
    </li>
  </ul>

  <svg class="back-mark" viewBox="0 0 150 150" role="img" aria-label="ChoiceCraft icon">
    <circle cx="75" cy="75" r="73" fill="var(--mark-dark)"/>
  </svg>
</section>

</body>
</html>
```